business card for a massage therapy practice named 'Cedar and Willow Massage Studio'

I really need a trendy, yet easy on the eyes business card to complement my logo. Ideally with some gold or rose gold foil work.

My uploaded file of the logo I have in horizontal but I have a vertical version as well. Another color that is used in the website is a blush pink here and there. I'd like to see some trendy tropical leaves in the design.

```html
<!DOCTYPE html>
<html lang="en">
<head>
<meta charset="utf-8">
<title>Cedar &amp; Willow Massage Studio – Business Card</title>
<link rel="stylesheet" href="https://fonts.googleapis.com/css2?family=Open+Sans:wght@400;600&display=swap">
<style>
  :root {
    --stage: #e4e2de;
    --card-light: #eeeeee;
    --card-gold: #9b8560;
    --gold: #a48a5c;
    --ink: #222222;
    --mint: #7fd6bb;
    --rule: #6a6a6a;
    --white: #ffffff;
  }
  * { margin: 0; padding: 0; box-sizing: border-box; }
  html, body {
    width: 1200px; height: 1200px; overflow: hidden;
    background: var(--stage);
    font-family: "Open Sans", sans-serif;
  }
  .canvas { position: relative; width: 1200px; height: 1200px; }
  .card {
    position: absolute; top: 310px; width: 366px; height: 594px;
    text-align: center; overflow: hidden;
  }
  .card--front { left: 233px; background: var(--card-light); color: var(--ink); }
  .card--back { left: 628px; background: var(--card-gold); color: var(--white); }

  .brand {
    position: absolute; top: 140px; left: 0; right: 0;
    display: flex; align-items: center; justify-content: center; gap: 14px;
  }
  .brand__dot { width: 46px; height: 46px; border-radius: 50%; flex: none; }
  .card--front .brand__dot { background: var(--gold); }
  .card--back .brand__dot { background: var(--white); }
  .brand__name {
    font-weight: 400; line-height: 1.15; text-align: center;
  }
  .brand__title { display: block; font-size: 30px; }
  .brand__sub { display: block; font-size: 16px; letter-spacing: 4px; text-transform: uppercase; margin-top: 4px; }
  .card--front .brand__name { color: var(--ink); }
  .card--back .brand__name { color: var(--white); }

  .contact { position: absolute; top: 374px; left: 0; right: 0; }
  .contact__name { color: var(--mint); font-size: 22px; font-weight: 400; line-height: 1.2; letter-spacing: .3px; }
  .contact__role { font-size: 17px; line-height: 1.3; }
  .contact__rule { width: 192px; height: 1px; background: var(--rule); margin: 10px auto 8px; }
  .contact__line { font-size: 17px; line-height: 22px; }

  .backdrop {
    position: absolute; left: 70px; top: 40px; width: 260px; height: 480px;
    border-radius: 50%; background: rgba(255,255,255,.06);
  }
  .services { position: absolute; top: 332px; left: 0; right: 0; list-style: none; }
  .services li { font-size: 15px; line-height: 29px; text-transform: uppercase; letter-spacing: .2px; }
  .follow {
    position: absolute; top: 522px; left: 52px; right: 52px;
    display: flex; align-items: center; gap: 8px; font-size: 15px; text-transform: uppercase;
  }
  .follow::before, .follow::after { content: ""; flex: 1; height: 1px; background: rgba(255,255,255,.7); }
  .social { position: absolute; top: 549px; left: 0; right: 0; display: flex; justify-content: center; gap: 6px; }
  .social span { width: 22px; height: 22px; border-radius: 50%; background: var(--white); }
</style>
</head>
<body>
<main class="canvas">
  <section class="card card--front">
    <div class="brand">
      <span class="brand__dot"></span>
      <p class="brand__name"><span class="brand__title">Cedar &amp; Willow</span><span class="brand__sub">Massage Studio</span></p>
    </div>
    <div class="contact">
      <h1 class="contact__name">MARISOL VEGA</h1>
      <p class="contact__role">Massage Theraphist</p>
      <div class="contact__rule"></div>
      <p class="contact__line">482 Alder Ave. suite 210</p>
      <p class="contact__line">Fairview, CA 95000</p>
      <div class="contact__rule"></div>
      <p class="contact__line">(555) 214-7380</p>
      <p class="contact__line">cedarandwillow@mail.com</p>
    </div>
  </section>

  <section class="card card--back">
    <div class="backdrop" role="img" aria-label="Faint large brand emblem in the background"></div>
    <div class="brand">
      <span class="brand__dot"></span>
      <p class="brand__name"><span class="brand__title">Cedar &amp; Willow</span><span class="brand__sub">Massage Studio</span></p>
    </div>
    <ul class="services">
      <li>Clinical Bodywork</li>
      <li>Therapeutic Massage</li>
      <li>Integrated Hot Stone Massage</li>
      <li>Lymphatic Drainage Massage</li>
      <li>Fairview Sinus Facial</li>
      <li>Australian Foot Treatment</li>
    </ul>
    <p class="follow">Follow us on</p>
    <div class="social" aria-label="Social media links">
      <span></span><span></span><span></span><span></span>
    </div>
  </section>
</main>
</body>
</html>
```